A business card design for a dental office. We have Two doctors working here. We practice general de

I already have a logo designed for the office with the name and a slogan.
Now I need to create design for a business card using the same logo.
Details Needed on the front side of the card are :
Bernard K. Oswin, DDS
Gerald M Fenwick, DDS
418 Birch Lane
Larkfield, ST 00000
Phone : 555 019 4831
Fax : 555 019 4832
Website : WWW.BrightmoorToothHaven.Com
Office hours by appointment
On the back side of the card need :
Appointment
Date....................Time...................
With....................................
If unable to keep your appointment, please give 24-48 hours notice in order to avoid broken appointment fee.

Industry/Entity Type

Dental Clinic

Contact Information for Business Card

Bernard K. Oswin, DDS
Gerald M Fenwick, DDS
418 Birch Lane
Larkfield, ST 00000
Phone : 555 019 4831
Fax : 555 019 4832
Appointment

Requirements
Must have
• Keep the Name and slogan on the logo on the front of the card. You can move them around the Logo and Name/Slogan of business (Oswin Family Dentistry/We give you reasons to smile) as you wish to get a feel of the design.
• Bernard K. Oswin, DDS
• Gerald M Fenwick, DDS
• 418 Birch Lane
• Larkfield, ST 00000
• Phone : 555 019 4831
• Fax : 555 019 4832
• WWW.BrightmoorToothHaven.Com
• Keep these three groups above as they are together now in different areas of the front side.
• On the back side of the card need :
• Appointment
• Date....................Time...................
• With....................................
• If unable to keep your appointment, please give 24-48 hours notice in order to avoid broken appointment fee.

```html
<!DOCTYPE html>
<html lang="en">
<head>
<meta charset="utf-8">
<title>Oswin Family Dentistry – Business Card</title>
<link rel="stylesheet" href="https://fonts.googleapis.com/css2?family=Arimo:wght@700&family=Cinzel:wght@600;700&display=swap">
<style>
  :root {
    --page-bg: #e9eaeb;
    --card-bg: #ffffff;
    --brand-blue: #285ea6;
    --brand-teal: #15a58b;
    --brand-red: #e0403a;
    --mark-fill: #dce9f5;
    --rule-blue: #8ea6cf;
    --text-white: #ffffff;
  }
  * { box-sizing: border-box; margin: 0; padding: 0; }
  html, body { width: 994px; height: 1200px; overflow: hidden; }
  body { background: var(--page-bg); position: relative; font-family: "Cinzel", serif; }

  .card {
    position: absolute;
    width: 752px;
    height: 452px;
    background: var(--card-bg);
    overflow: hidden;
    box-shadow: 0 6px 10px rgba(0,0,0,0.18);
  }
  .card--front { left: 110px; top: 138px; }
  .card--back  { left: 115px; top: 666px; }

  .card__shape { position: absolute; inset: 0; width: 100%; height: 100%; }

  .brand-mark {
    position: absolute;
    width: 124px;
    display: flex;
    flex-direction: column;
    align-items: center;
  }
  .brand-mark__dot {
    width: 110px; height: 110px; border-radius: 50%;
    background: var(--mark-fill);
  }
  .brand-mark__name {
    margin-top: 6px;
    font-family: "Cinzel", serif; font-weight: 700;
    font-size: 18px; letter-spacing: 1px;
    color: var(--brand-blue);
  }
  .card--front .brand-mark { left: 72px; top: 38px; }
  .card--back .brand-mark { left: 36px; top: 14px; }
  .card--back .brand-mark__dot { width: 96px; height: 96px; }
  .card--back .brand-mark__name { color: var(--text-white); margin-top: 2px; font-size: 17px; }

  /* Front */
  .practice {
    position: absolute; left: 230px; width: 490px; top: 34px;
    text-align: center;
  }
  .practice__name {
    font-family: "Arimo", sans-serif; font-weight: 700;
    font-size: 28px; letter-spacing: 0.8px;
    color: var(--brand-blue); text-transform: uppercase;
  }
  .practice__slogan {
    margin-top: 8px;
    display: flex; align-items: center; justify-content: center; gap: 8px;
    font-family: "Arimo", sans-serif; font-size: 11.5px; letter-spacing: 1.4px;
    color: var(--brand-red); text-transform: uppercase;
  }
  .practice__slogan::before, .practice__slogan::after {
    content: ""; width: 32px; height: 1px; background: var(--brand-red);
  }
  .practice__web {
    margin-top: 16px;
    font-size: 16.5px; font-weight: 700; letter-spacing: 1px;
    color: var(--brand-blue);
  }
  .practice__address {
    margin-top: 14px;
    font-size: 17.5px; font-weight: 700; letter-spacing: 0.8px;
    color: var(--brand-teal);
  }

  .doctors {
    position: absolute; right: 340px; top: 268px;
    text-align: right; color: var(--text-white);
    font-size: 19px; font-weight: 700; letter-spacing: 0.6px; line-height: 31px;
  }
  .divider {
    position: absolute; left: 432px; top: 262px;
    width: 2px; height: 89px; background: var(--text-white);
  }
  .contact {
    position: absolute; left: 453px; top: 268px;
    list-style: none; color: var(--text-white);
    font-family: "Arimo", sans-serif; font-weight: 700;
    font-size: 18px; letter-spacing: 3.2px; line-height: 31px;
  }
  .contact__item { display: flex; align-items: center; gap: 12px; }
  .contact__icon { width: 20px; height: 20px; fill: var(--text-white); }
  .hours {
    position: absolute; left: 0; right: 0; top: 378px;
    padding-left: 100px; text-align: center;
    color: var(--text-white);
    font-size: 13px; font-weight: 700; letter-spacing: 2px;
  }

  /* Back */
  .appointment__title {
    position: absolute; left: 230px; width: 420px; top: 38px;
    text-align: center; color: var(--text-white);
    font-size: 21px; font-weight: 700; letter-spacing: 1px;
  }
  .appointment__fields { position: absolute; left: 196px; top: 140px; width: 490px; }
  .field {
    display: flex; align-items: flex-end; height: 75px;
    color: var(--brand-blue); font-size: 20px; font-weight: 700; letter-spacing: 1px;
  }
  .field__label { width: 76px; line-height: 1; }
  .field__line { flex: 1; height: 1px; background: var(--rule-blue); margin-bottom: 4px; }
  .field:first-child { height: 28px; }
  .appointment__note {
    position: absolute; left: 40px; right: 40px; top: 378px;
    text-align: center; color: var(--brand-blue);
    font-size: 13px; font-weight: 700; letter-spacing: 1.6px; line-height: 21px;
  }
</style>
</head>
<body>

<section class="card card--front" aria-label="Business card front">
  <svg class="card__shape" viewBox="0 0 752 452" preserveAspectRatio="none" aria-hidden="true">
    <path d="M0 228 C70 222 120 208 170 196 C200 188 215 184 228 184 L752 184 L752 452 L0 452 Z" fill="var(--brand-blue)"/>
    <rect x="226" y="182" width="526" height="3" fill="var(--brand-teal)"/>
  </svg>

  <div class="brand-mark">
    <div class="brand-mark__dot"></div>
    <div class="brand-mark__name">Oswin</div>
  </div>

  <header class="practice">
    <h1 class="practice__name">Oswin Family Dentistry</h1>
    <p class="practice__slogan">We give you reasons to smile</p>
    <p class="practice__web">WWW.BrightmoorToothHaven.Com</p>
    <p class="practice__address">418 Birch Lane Larkfield, ST 00000</p>
  </header>

  <div class="doctors">
    <p>Bernard K. Oswin, DDS</p>
    <p>Gerald M Fenwick, DDS</p>
  </div>
  <div class="divider"></div>
  <ul class="contact">
    <li class="contact__item">
      <svg class="contact__icon" viewBox="0 0 24 24" aria-label="Phone"><path d="M6.6 2.5l3 3.4-1.9 2.4c1 2.6 3.3 5.3 6 6.6l2.3-1.8 3.5 2.9-1.6 3.3C10.4 19.6 4.1 12 4.5 4.2z"/></svg>
      <span>555 019 4831</span>
    </li>
    <li class="contact__item">
      <svg class="contact__icon" viewBox="0 0 24 24" aria-label="Fax"><path d="M6 2h10v6H6zM3 10h18v11H3zm3 3v2h12v-2zm0 4v2h5v-2z"/></svg>
      <span>555 019 4832</span>
    </li>
  </ul>
  <p class="hours">Office hours by appointment</p>
</section>

<section class="card card--back" aria-label="Business card back">
  <svg class="card__shape" viewBox="0 0 751 452" preserveAspectRatio="none" aria-hidden="true">
    <path d="M0 0 L751 0 L751 80 L200 80 C175 80 160 108 142 128 C112 160 50 172 0 172 Z" fill="var(--brand-blue)"/>
    <rect x="198" y="79" width="553" height="3" fill="var(--brand-teal)"/>
  </svg>

  <div class="brand-mark">
    <div class="brand-mark__dot"></div>
    <div class="brand-mark__name">Oswin</div>
  </div>

  <h2 class="appointment__title">Appointment:</h2>
  <div class="appointment__fields">
    <div class="field"><span class="field__label">Date</span><span class="field__line"></span></div>
    <div class="field"><span class="field__label">Time</span><span class="field__line"></span></div>
    <div class="field"><span class="field__label">With</span><span class="field__line"></span></div>
  </div>
  <p class="appointment__note">If unable to keep your appointment, please give 24-48 hours<br>notice in order to avoid broken appointment fee.</p>
</section>

</body>
</html>
```